Need help in designing new business card utilizing our new logo.

BuildMark Solutions works with Construction Business Owners, Managers & IT Professionals to strengthen software usage and increase user productivity.

Our Construction Accounting and Mobile Field Management Software Clients engage with us in the following areas:

New Software Implementations
Software Re-Implementations
Redesigning Software Usage at the User Level
Project Coordination & Management
Continued Software Support

Old tag line:
Mapping Choices - Delivering Results

www.buildmark-solutions.example

Ridge 4 is a product, but not needed for a new business card.

```html
<!DOCTYPE html>
<html lang="en">
<head>
<meta charset="utf-8">
<title>BuildMark Solutions – Business Card</title>
<link rel="stylesheet" href="https://fonts.googleapis.com/css2?family=Jost:wght@400;500&family=Montserrat:wght@600&family=Oswald:wght@500&display=swap">
<style>
  :root {
    --backdrop: #3a3a3a;
    --card: #262626;
    --ink: #f2f2f2;
    --ink-soft: #cfcfcf;
    --silver: #a9a9a9;
    --accent: #3b4fc4;
    --accent-line: #3f5fd6;
  }
  * { margin: 0; padding: 0; box-sizing: border-box; }
  html, body { width: 1200px; height: 899px; overflow: hidden; }
  body {
    background: var(--backdrop);
    font-family: "Jost", "Helvetica Neue", Arial, sans-serif;
    color: var(--ink);
    position: relative;
  }
  .card {
    position: absolute;
    left: 260px;
    width: 680px;
    height: 389px;
    background: var(--card);
    box-shadow: 0 6px 18px rgba(0,0,0,.45);
  }
  .card--front { top: 40px; }
  .card--back { top: 470px; }

  .brand {
    position: absolute;
    display: flex;
    align-items: center;
    gap: 14px;
  }
  .brand__mark { width: 46px; height: 46px; }
  .brand__name {
    font-family: "Montserrat", "Helvetica Neue", Arial, sans-serif;
    font-weight: 600;
    line-height: 1.05;
    text-transform: uppercase;
  }
  .brand__name span { display: block; }
  .brand__name .brand__sub { letter-spacing: .42em; }

  .card--front .brand { left: 0; right: 0; top: 118px; justify-content: center; }
  .card--front .brand__mark { fill: var(--silver); }
  .card--front .brand__name { color: var(--silver); font-size: 40px; }
  .card--front .brand__name .brand__sub { font-size: 16px; }
  .tagline {
    position: absolute;
    left: 0; right: 0; top: 306px;
    text-align: center;
    font-size: 17px;
    letter-spacing: .04em;
    color: var(--ink-soft);
  }

  .card--back .brand { right: 44px; top: 44px; gap: 10px; }
  .card--back .brand__mark { width: 34px; height: 34px; fill: var(--accent); }
  .card--back .brand__name { color: var(--accent); font-size: 30px; }
  .card--back .brand__name .brand__sub { font-size: 12px; }

  .person { position: absolute; left: 50px; top: 122px; }
  .person__name {
    font-family: "Oswald", "Arial Narrow", sans-serif;
    font-weight: 500;
    font-size: 36px;
    letter-spacing: .01em;
    text-transform: uppercase;
    line-height: 1;
  }
  .person__role { font-size: 19px; font-weight: 500; margin-top: 2px; }

  .divider {
    position: absolute;
    left: 50px; right: 44px; top: 208px;
    height: 2px;
    background: var(--accent-line);
  }

  .contacts {
    position: absolute;
    left: 50px; top: 224px;
    list-style: none;
    font-size: 17px;
    line-height: 28px;
  }
  .contacts li { display: flex; align-items: center; gap: 10px; }
  .contacts svg { width: 18px; height: 18px; fill: none; stroke: var(--accent-line); stroke-width: 2; }
  .contacts svg.solid { fill: var(--accent-line); stroke: none; }

  .address {
    position: absolute;
    right: 44px; top: 300px;
    font-size: 17px;
    line-height: 26px;
    text-align: right;
    font-style: normal;
  }
</style>
</head>
<body>
  <section class="card card--front" aria-label="Card front">
    <div class="brand">
      <svg class="brand__mark" viewBox="0 0 46 46" aria-hidden="true"><rect width="46" height="46"/></svg>
      <div class="brand__name"><span>BuildMark</span><span class="brand__sub">Solutions</span></div>
    </div>
    <p class="tagline">Mapping Choices - Delivering Results</p>
  </section>

  <section class="card card--back" aria-label="Card back">
    <div class="brand">
      <svg class="brand__mark" viewBox="0 0 34 34" aria-hidden="true"><rect width="34" height="34"/></svg>
      <div class="brand__name"><span>BuildMark</span><span class="brand__sub">Solutions</span></div>
    </div>

    <div class="person">
      <h1 class="person__name">Dana R. Whitfield</h1>
      <p class="person__role">Owner</p>
    </div>

    <div class="divider"></div>

    <ul class="contacts">
      <li><svg viewBox="0 0 24 24" aria-hidden="true"><path d="M5 4c3 0 4 4 3 5l-2 1c1 3 4 6 7 7l1-2c1-1 5 0 5 3 0 2-2 3-4 3C9 21 3 15 3 8c0-2 1-4 2-4z"/></svg>800-555-0142 ext.100</li>
      <li><svg viewBox="0 0 24 24" aria-hidden="true"><rect x="6" y="2" width="12" height="20" rx="2"/><path d="M10 18h4"/></svg>555-014-7290</li>
      <li><svg class="solid" viewBox="0 0 24 24" aria-hidden="true"><path d="M2 5h20v2l-10 6L2 7z"/><path d="M2 9l10 6 10-6v10H2z"/></svg>dana.whitfield@buildmark-solutions.example</li>
      <li><svg viewBox="0 0 24 24" aria-hidden="true"><circle cx="14" cy="10" r="6"/><path d="M9.5 14.5 3 21"/></svg>www.buildmark-solutions.example</li>
    </ul>

    <address class="address">
      14b Harbor Lane - PMB 118<br>
      Maple Falls NY 10501
    </address>
  </section>
</body>
</html>
```